Etikett für Rotweinflasche
Liebe farbkosmos Atelier, wir werden uns bei der endgültigen Etikettengestaltung (finale Größe + Rückseite) noch an Euch melden. Bitte sendet uns euren Kontakt an helga.brandt@morvelli.wine
Zielgruppe
Morvelli Italia ist ein exklusives Boutique-Weingut in Sizilien, das hochqualitative Spitzenweine in kleinen Mengen mit modernster Technologie und stets nachhaltig erzeugt. Wir hinterfragen sowohl in der Agronomie im Weingarten als auch in der Önologie im Weinkeller alle herrschenden Traditionen und trachten danach, stets das beste Endprodukt zu kreieren. Der vulkanische, kalkreiche Boden Siziliens sowie trockene, sonnenreiche und niederschlagsarme Vegetationsperioden sind unsere optimale Basis.
Zielgruppe: Internationale Genussmenschen jeglichen Alters, die sich bewusst auch höherpreisige Weine (um die €30+) gönnen , vor allem kunstaffine young professionals mit Qualitäts-& Nachhaltigkeitsanspruch
Aufgabenstellung
Das Etikett ist für Rotwein-Flaschen (Cabernet Sauvignon / Nero D'Avola / Frappato / Syrah / Cerasuolo / Petit Verdot / sowie einen Bourdeaux-Cuveè aus Cabernet Sauvignon und Petit Verdot) .
Die Flasche ist reinschwarz, sehr hochwertig und schwer.
Flaschenform: Bordeauxflasche siehe technisches Datenblatt
Sleeve über dem Korken: schwarz mit weißer Schrift wie bisher
Zu gestalten ist das Etikett der Vorderseite. Zumindest die jeweilige Rotwein-Sorte ist auch textlich darzustellen (zwecks Scannen mit Trubel-App)
Der Kreativität kann freien Lauf gelassen werden! Unterscheidbarkeit vom Markt ist explizit gewollt.
Unsere aktuellen Etiketten und Markenauftritt siehe: https://morvelli.wine/shop/

```html
<!DOCTYPE html>
<html lang="de">
<head>
<meta charset="utf-8">
<title>Cabernet Sauvignon – Etikett</title>
<link rel="stylesheet" href="https://fonts.googleapis.com/css2?family=EB+Garamond:wght@400;500&display=swap">
<style>
  :root {
    --backdrop: #3b3d42;
    --label-shadow: rgba(0, 0, 0, 0.35);
    --sea-light: #9fd3d0;
    --sea-mid: #4fa5ad;
    --sea-deep: #2f5f86;
    --bloom-magenta: #d2327f;
    --bloom-violet: #4a2f9a;
    --bloom-gold: #f2b632;
    --type-white: #f4f4f2;
  }
  html, body {
    margin: 0;
    padding: 0;
    width: 1200px;
    height: 900px;
    overflow: hidden;
    background: var(--backdrop);
  }
  .canvas {
    position: relative;
    width: 1200px;
    height: 900px;
    display: flex;
    align-items: center;
    justify-content: center;
  }
  .wine-label {
    position: relative;
    width: 480px;
    height: 660px;
    overflow: hidden;
    box-shadow: 0 18px 40px var(--label-shadow);
  }
  .label-artwork {
    position: absolute;
    inset: 0;
    width: 100%;
    height: 100%;
    display: block;
  }
  .varietal {
    position: absolute;
    top: 44px;
    left: 44px;
    margin: 0;
    font-family: "EB Garamond", "Times New Roman", serif;
    font-weight: 400;
    font-size: 40px;
    line-height: 1.02;
    letter-spacing: 0.02em;
    text-transform: uppercase;
    color: var(--type-white);
  }
  .varietal span { display: block; }
</style>
</head>
<body>
  <main class="canvas">
    <article class="wine-label">
      <svg class="label-artwork" viewBox="0 0 480 660" role="img" aria-label="Illustration: leuchtende Qualle in Magenta, Violett und Gold mit langen Tentakeln im türkisblauen Meer">
        <defs>
          <linearGradient id="sea" x1="0" y1="0" x2="1" y2="1">
            <stop offset="0" stop-color="var(--sea-light)"/>
            <stop offset="0.5" stop-color="var(--sea-mid)"/>
            <stop offset="1" stop-color="var(--sea-deep)"/>
          </linearGradient>
          <radialGradient id="bloom" cx="0.62" cy="0.55" r="0.55">
            <stop offset="0" stop-color="var(--bloom-magenta)" stop-opacity="0.85"/>
            <stop offset="0.45" stop-color="var(--bloom-violet)" stop-opacity="0.55"/>
            <stop offset="1" stop-color="var(--bloom-violet)" stop-opacity="0"/>
          </radialGradient>
          <radialGradient id="glow" cx="0.25" cy="0.88" r="0.3">
            <stop offset="0" stop-color="var(--bloom-gold)" stop-opacity="0.7"/>
            <stop offset="1" stop-color="var(--bloom-gold)" stop-opacity="0"/>
          </radialGradient>
        </defs>
        <rect width="480" height="660" fill="url(#sea)"/>
        <rect width="480" height="660" fill="url(#bloom)"/>
        <rect width="480" height="660" fill="url(#glow)"/>
      </svg>
      <h1 class="varietal"><span>Cabernet</span><span>Sauvignon</span></h1>
    </article>
  </main>
</body>
</html>
```